Telecommunications/Power civil contractor needs business card design

Were a new telecommunications/power underground civil contractor that is looking for a new business card design. Our company colours are silver or grey and orange. Feel free to use the white background logo or the black background logo.

Target Market(s)

Local contractors, utility companies, private sector mining/energy companies, developers.

Industry/Entity Type

Telecommunications

Contact Information for Business Card

Each card will need the following info:
Persons name:
Title:
E-mail:
Phone number:
Shop Address:
Mailing Address:

Requirements
Must have
• Each card will need the following info:
• Persons name:
• Title:
• E-mail:
• Phone number:
• Shop Address:
• Mailing Address:

```html
<!DOCTYPE html>
<html lang="en">
<head>
<meta charset="utf-8">
<title>Tamrack Civil Works Inc – Business Card</title>
<link rel="stylesheet" href="https://fonts.googleapis.com/css2?family=Open+Sans:wght@400;600;700&display=swap">
<style>
  :root {
    --backdrop: #3a332f;
    --card: #0e0e0e;
    --orange: #f15a24;
    --silver: #9a9a9a;
    --text: #f2f2f2;
  }
  * { margin: 0; padding: 0; box-sizing: border-box; }
  html, body {
    width: 1200px;
    height: 900px;
    overflow: hidden;
  }
  body {
    background: var(--backdrop);
    font-family: "Open Sans", Arial, sans-serif;
    position: relative;
  }
  .card {
    position: absolute;
    top: 295px;
    width: 540px;
    height: 310px;
    background: var(--card);
    border-radius: 3px;
    box-shadow: 0 10px 24px rgba(0,0,0,0.45);
  }
  .card--contact { left: 45px; }
  .card--brand { left: 615px; }

  /* Contact side */
  .brand-mark {
    position: absolute;
    left: 30px;
    top: 70px;
    width: 220px;
    height: 170px;
    display: flex;
    flex-direction: column;
    align-items: center;
    justify-content: center;
    gap: 14px;
  }
  .brand-mark__circle {
    width: 96px;
    height: 96px;
    border-radius: 50%;
    border: 5px solid var(--silver);
  }
  .brand-mark__name {
    color: var(--orange);
    font-weight: 700;
    font-size: 17px;
    letter-spacing: 0.5px;
    text-align: center;
    line-height: 1.2;
  }
  .divider {
    position: absolute;
    left: 268px;
    top: 80px;
    width: 2px;
    height: 150px;
    background: linear-gradient(to bottom, transparent, var(--orange) 40%, var(--orange) 60%, transparent);
  }
  .details {
    position: absolute;
    left: 292px;
    top: 46px;
    color: var(--text);
    font-size: 14px;
    line-height: 1.35;
  }
  .details__name {
    color: var(--orange);
    font-weight: 600;
    font-size: 17px;
    line-height: 1.25;
  }
  .details__title {
    color: var(--silver);
    font-size: 13px;
    margin-bottom: 7px;
  }
  .details__row {
    display: flex;
    align-items: center;
    gap: 8px;
  }
  .details__row svg { width: 12px; height: 12px; fill: var(--orange); }
  .details__heading {
    color: var(--orange);
    font-weight: 600;
    font-size: 16px;
    margin-top: 8px;
  }

  /* Brand side */
  .brand-face {
    position: absolute;
    inset: 0;
    display: flex;
    flex-direction: column;
    align-items: center;
    justify-content: center;
    gap: 20px;
  }
  .brand-face__circle {
    width: 96px;
    height: 96px;
    border-radius: 50%;
    border: 5px solid var(--silver);
  }
  .brand-face__name {
    color: var(--orange);
    font-weight: 700;
    font-size: 28px;
    letter-spacing: 1px;
    text-transform: uppercase;
    text-align: center;
    line-height: 1.15;
  }
</style>
</head>
<body>
  <section class="card card--contact">
    <div class="brand-mark">
      <div class="brand-mark__circle"></div>
      <div class="brand-mark__name">Tamrack Civil<br>Works Inc</div>
    </div>
    <div class="divider"></div>
    <div class="details">
      <p class="details__name">Daniel Reyes</p>
      <p class="details__title">Project Manager</p>
      <p class="details__row">
        <svg viewBox="0 0 24 24" aria-hidden="true"><path d="M6.6 10.8a15.1 15.1 0 0 0 6.6 6.6l2.2-2.2a1 1 0 0 1 1-.25 11.4 11.4 0 0 0 3.6.57 1 1 0 0 1 1 1V20a1 1 0 0 1-1 1A17 17 0 0 1 3 4a1 1 0 0 1 1-1h3.5a1 1 0 0 1 1 1c0 1.25.2 2.45.57 3.57a1 1 0 0 1-.25 1z"/></svg>
        044-555 019 274
      </p>
      <p class="details__row">
        <svg viewBox="0 0 24 24" aria-hidden="true"><path d="M2 6.5V19h20V6.5l-10 7.5z M2.5 5h19L12 12z"/></svg>
        hello@tamrackcivil.com
      </p>
      <p class="details__heading">Shop Address</p>
      <p>12345, Address Goes Here</p>
      <p>Country Name, 123456.</p>
      <p class="details__heading">Mailing Address</p>
      <p>12345, Address Goes Here</p>
      <p>Country Name, 123456.</p>
    </div>
  </section>

  <section class="card card--brand">
    <div class="brand-face">
      <div class="brand-face__circle"></div>
      <div class="brand-face__name">Tamrack Civil<br>Works Inc</div>
    </div>
  </section>
</body>
</html>
```